Harborline Auto LLC

Car Dealer Customer Service
Address: 2874 Cresthaven Road, Shelbyville, TN 37162
web: www.harborlineautoxq.net
email: harborlineautoxq@mailnest.example
Phone: (931) 555-0148
Phone: (629) 555-0173

```html
<!DOCTYPE html>
<html lang="en">
<head>
<meta charset="utf-8">
<title>Harborline Auto LLC — Business Card</title>
<link href="https://fonts.googleapis.com/css2?family=Poppins:wght@400;500;700&family=Lexend:wght@700&display=swap" rel="stylesheet">
<style>
  :root {
    --bg: #2b2b2b;
    --brand-blue: #1e7fb6;
    --brand-blue-deep: #17659a;
    --ink-blue: #15608f;
    --gold: #dca63d;
    --card-white: #f2f2f2;
    --ink: #222222;
    --white: #ffffff;
  }
  * { margin: 0; padding: 0; box-sizing: border-box; }
  html, body {
    width: 1200px; height: 1138px; overflow: hidden;
    background: var(--bg);
    font-family: "Poppins", sans-serif;
  }
  .canvas { position: relative; width: 1200px; height: 1138px; }
  .card {
    position: absolute;
    width: 620px; height: 375px;
    border-radius: 16px;
    overflow: hidden;
  }
  .card--front {
    left: 274px; top: 186px;
    background: linear-gradient(135deg, var(--brand-blue) 0%, var(--brand-blue-deep) 100%);
  }
  .card--back {
    left: 276px; top: 608px;
    background: var(--card-white);
  }
  .emblem-area {
    position: absolute;
    left: -70px; top: 14px;
    width: 344px; height: 344px;
    border-radius: 50%;
  }
  .card--front .emblem-area { background: #e9eff3; }
  .card--back .emblem-area { background: var(--brand-blue); top: 10px; }
  .brand-name {
    position: absolute;
    right: 41px;
    font-family: "Lexend", sans-serif;
    font-weight: 700;
    font-size: 27px;
    letter-spacing: 0.5px;
    text-transform: uppercase;
  }
  .card--front .brand-name { top: 55px; color: var(--white); }
  .card--back .brand-name { top: 40px; right: 26px; color: var(--ink-blue); }
  .front-web {
    position: absolute; right: 41px; bottom: 30px;
    color: var(--white); font-size: 14px;
  }
  .contact-block {
    position: absolute; right: 26px; top: 150px;
    text-align: right;
  }
  .person-name { color: var(--ink-blue); font-weight: 700; font-size: 23px; line-height: 1.2; }
  .person-role { color: var(--ink); font-size: 15px; margin-bottom: 22px; }
  .contact-line {
    display: flex; justify-content: flex-end; align-items: center;
    gap: 8px; font-size: 15px; color: var(--ink); line-height: 22px;
  }
  .contact-line--phone { color: var(--ink-blue); font-weight: 700; font-size: 16px; }
  .contact-line svg { width: 13px; height: 13px; fill: var(--gold); flex: none; }
  .contact-line--address { margin-top: 2px; }
</style>
</head>
<body>
<main class="canvas">
  <section class="card card--front">
    <div class="emblem-area" role="img" aria-label="Brand emblem area"></div>
    <h1 class="brand-name">Harborline Auto</h1>
    <p class="front-web">www.harborlineautoxq.net</p>
  </section>

  <section class="card card--back">
    <div class="emblem-area" role="img" aria-label="Brand emblem area"></div>
    <h2 class="brand-name">Harborline Auto</h2>
    <div class="contact-block">
      <p class="person-name">Daniel Mercer</p>
      <p class="person-role">Managing Director</p>
      <p class="contact-line contact-line--phone">931-555-0148
        <svg viewBox="0 0 24 24" aria-hidden="true"><path d="M6.6 10.8a15.1 15.1 0 0 0 6.6 6.6l2.2-2.2a1 1 0 0 1 1-.25 11.4 11.4 0 0 0 3.6.57 1 1 0 0 1 1 1V20a1 1 0 0 1-1 1A17 17 0 0 1 3 4a1 1 0 0 1 1-1h3.5a1 1 0 0 1 1 1c0 1.25.2 2.45.57 3.57a1 1 0 0 1-.25 1z"/></svg></p>
      <p class="contact-line contact-line--phone">629-555-0173
        <svg viewBox="0 0 24 24" aria-hidden="true"><path d="M6.6 10.8a15.1 15.1 0 0 0 6.6 6.6l2.2-2.2a1 1 0 0 1 1-.25 11.4 11.4 0 0 0 3.6.57 1 1 0 0 1 1 1V20a1 1 0 0 1-1 1A17 17 0 0 1 3 4a1 1 0 0 1 1-1h3.5a1 1 0 0 1 1 1c0 1.25.2 2.45.57 3.57a1 1 0 0 1-.25 1z"/></svg></p>
      <p class="contact-line" style="margin-top:4px">www.harborlineautoxq.net
        <svg viewBox="0 0 24 24" aria-hidden="true"><path d="M12 2a10 10 0 1 0 0 20 10 10 0 0 0 0-20zm6.9 6h-3a15.7 15.7 0 0 0-1.4-3.6A8 8 0 0 1 18.9 8zM12 4c.8 1.2 1.5 2.5 1.9 4h-3.8c.4-1.5 1.1-2.8 1.9-4zM4.3 14a8.2 8.2 0 0 1 0-4h3.4a16.5 16.5 0 0 0 0 4zm.8 2h3a15.7 15.7 0 0 0 1.4 3.6A8 8 0 0 1 5.1 16zm3-8h-3a8 8 0 0 1 4.4-3.6A15.7 15.7 0 0 0 8.1 8zM12 20c-.8-1.2-1.5-2.5-1.9-4h3.8c-.4 1.5-1.1 2.8-1.9 4zm2.3-6H9.7a14.7 14.7 0 0 1 0-4h4.6a14.7 14.7 0 0 1 0 4zm.2 5.6a15.7 15.7 0 0 0 1.4-3.6h3a8 8 0 0 1-4.4 3.6zm1.8-5.6a16.5 16.5 0 0 0 0-4h3.4a8.2 8.2 0 0 1 0 4z"/></svg></p>
      <p class="contact-line">harborlineautoxq@mailnest.example
        <svg viewBox="0 0 24 24" aria-hidden="true"><path d="M2 5h20v14H2zm2 2v.5l8 5 8-5V7zm0 2.9V17h16V9.9l-8 5z"/></svg></p>
      <p class="contact-line contact-line--address">2874 Cresthaven Road, Shelbyville, TN 37162</p>
    </div>
  </section>
</main>
</body>
</html>
```